Allied Health team of Physiotherapists & Occupational Therapists seek a business card design

We have our new logo, we now need our new business cards and stationary. Tidewell: Oedema & Family Clinic is seeking a generic card design to represent our whole team and individual cards for each therapist that incorporates our new logo to communicate our holistic approach that is calming, nuturing, supportive and welcoming.
Our Physiotherapists and Occupational Therapists assess, treat and provide education for people who are at risk of or who have lymphoedema. This is often as a result of treatment for cancer. We provide pre-operative and post-operative management and cancer rehabilitation in our Pilates studio. Our team also consists of Physiotherapists who have a strong interest in pelvic floor and continence management for both men and women.

Target Market(s)

Mainly women health conscious

Industry/Entity Type

Allied Health: Physiotherapy / Occupational Therapy

Contact Information for Business Card

Address: 14 Gallivant Ave Frankston 3199 Phone: 84316570 fax: 8431 6578 Email: info@tidewellcareservices.com.au Website: tidewellcareservices.com.au Facebook address: facebook.com/TidewellOedemaAndFamilyCareClinic. Room to write appointments. Individual cards need to have name, office email and individual email and professional details

Requirements
Must have
• Logo as per uploaded documents

```html
<!DOCTYPE html>
<html lang="en">
<head>
<meta charset="utf-8">
<title>Tidewell: Oedema &amp; Family Clinic – Business Card</title>
<link rel="stylesheet" href="https://fonts.googleapis.com/css2?family=Arimo:wght@400&family=Montserrat:wght@600&family=Open+Sans:wght@400&display=swap">
<style>
  :root {
    --backdrop: #ebe7e3;
    --card-white: #ffffff;
    --peach: #f8b186;
    --peach-edge: #f07a3e;
    --sage: #c3cdc4;
    --ink-light: #ffffff;
  }
  * { box-sizing: border-box; margin: 0; padding: 0; }
  html, body {
    width: 1200px; height: 960px; overflow: hidden;
    background: var(--backdrop);
  }
  .canvas { position: relative; width: 1200px; height: 960px; }

  .card {
    position: absolute; left: 300px; width: 600px; height: 344px;
    border-radius: 22px; overflow: hidden;
    box-shadow: 0 3px 6px rgba(0,0,0,0.28);
  }
  .card--front { top: 112px; background: var(--card-white); border-bottom: 3px solid var(--peach-edge); }
  .card--back { top: 472px; background: var(--peach); border-top: 2px solid var(--peach-edge); }

  .card__wave { position: absolute; inset: 0; width: 600px; height: 344px; }

  .brand-name {
    position: absolute; font-family: "Arimo", Arial, sans-serif; font-weight: 400;
    text-align: center; line-height: 1.25;
  }
  .card--front .brand-name {
    left: 50px; top: 92px; width: 200px; font-size: 19px; color: var(--peach);
  }
  .card--back .brand-name {
    left: 150px; top: 132px; width: 300px; font-size: 27px; color: var(--ink-light);
  }

  .person { position: absolute; right: 34px; top: 120px; text-align: right; color: var(--ink-light); }
  .person__name {
    font-family: "Montserrat", sans-serif; font-weight: 600;
    font-size: 11.5px; letter-spacing: 2.6px; line-height: 1;
  }
  .person__role { font-family: "Open Sans", sans-serif; font-size: 7px; margin-top: 2px; }

  .contact-list { position: absolute; right: 36px; top: 178px; list-style: none; }
  .contact-list__item {
    display: flex; align-items: center; justify-content: flex-end;
    height: 34px; font-family: "Arimo", Arial, sans-serif; font-size: 17.5px; color: var(--ink-light);
  }
  .contact-list__icon { width: 18px; height: 18px; margin-left: 16px; flex: none; }

  .address {
    position: absolute; left: 19px; bottom: 18px;
    font-family: "Arimo", Arial, sans-serif; font-size: 14.5px; color: var(--ink-light);
  }
</style>
</head>
<body>
<main class="canvas">

  <section class="card card--front" aria-label="Card front">
    <svg class="card__wave" viewBox="0 0 600 344" aria-hidden="true">
      <path fill="var(--sage)" d="M0,212 C80,262 170,300 262,236 S470,44 560,46 L600,54 L600,344 L0,344 Z"/>
      <path fill="var(--peach)" stroke="#ffffff" stroke-width="2.5"
            d="M0,240 C80,282 168,318 266,258 S478,58 566,62 L602,66 L602,346 L-2,346 Z"/>
    </svg>

    <p class="brand-name">Tidewell: Oedema &amp; Family Clinic</p>

    <div class="person">
      <p class="person__name">JORDAN MARSH</p>
      <p class="person__role">CEO/Managing Director</p>
    </div>

    <ul class="contact-list">
      <li class="contact-list__item">123 456 7890
        <svg class="contact-list__icon" viewBox="0 0 24 24" fill="none" stroke="#fff" stroke-width="1.8" stroke-linecap="round" stroke-linejoin="round" aria-hidden="true">
          <path d="M6 3l3 4-2 2c1 3 4 6 7 7l2-2 4 3-2 3C11 20 4 13 3 5z"/>
        </svg>
      </li>
      <li class="contact-list__item">123 465 7890
        <svg class="contact-list__icon" viewBox="0 0 24 24" fill="none" stroke="#fff" stroke-width="1.8" aria-hidden="true">
          <rect x="6" y="1.5" width="12" height="21" rx="2"/><circle cx="12" cy="19" r="0.9" fill="#fff"/>
        </svg>
      </li>
      <li class="contact-list__item">hello@yourmailbox.com
        <svg class="contact-list__icon" viewBox="0 0 24 24" fill="none" stroke="#fff" stroke-width="1.8" aria-hidden="true">
          <rect x="2" y="5" width="20" height="14"/><path d="M2 5l10 8 10-8M2 19l7-7M22 19l-7-7"/>
        </svg>
      </li>
      <li class="contact-list__item">www.yoursitehere.com
        <svg class="contact-list__icon" viewBox="0 0 24 24" fill="none" stroke="#fff" stroke-width="1.6" aria-hidden="true">
          <circle cx="12" cy="12" r="10"/><ellipse cx="12" cy="12" rx="4.5" ry="10"/><path d="M2 12h20M4 7h16M4 17h16"/>
        </svg>
      </li>
    </ul>

    <p class="address">48 Kestrel Row Ashbury, VA, US</p>
  </section>

  <section class="card card--back" aria-label="Card back">
    <p class="brand-name">Tidewell: Oedema &amp; Family Clinic</p>
  </section>

</main>
</body>
</html>
```